business card for horse saddlery

after a new business card for our saddlery, i will add 2 logos we have previously used and they can be used (or not) . Any images can be used from our website also at www.harrowfields.net.au, I have also added our brand logo, which may be good to incorporate on back ? we have over 15, 000 items online, ship Australia Wide.

Target Market(s)

horse owners

Industry/Entity Type

Retail - Equestrian

Contact Information for Business Card

Harrowfield Horse Supplies, 1300 48 62 90, www.harrowfields.net.au, 27 Lindqvist Rd Marrowbank Q 4587

Requirements
Must have
• trailgem is our brand so trailgem logo on back as 'distributers of', easy to read
Nice to have
• professional but fun
Should not have
• double sided (description wont save double sided)

```html
<!DOCTYPE html>
<html lang="en">
<head>
<meta charset="utf-8">
<title>Harrowfield Horse Supplies – Business Card</title>
<link href="https://fonts.googleapis.com/css2?family=Lato:wght@400;700;900&display=swap" rel="stylesheet">
<style>
  :root {
    --backdrop: #2a2b2e;
    --card: #ffffff;
    --ink-blue: #3a55c8;
    --deep-blue: #2f4fb8;
    --sky-blue: #47b9ec;
    --brand-navy: #1d3f86;
    --brand-grey: #3a3d42;
  }
  html, body {
    margin: 0;
    width: 1200px;
    height: 800px;
    overflow: hidden;
    background: var(--backdrop);
    font-family: "Lato", sans-serif;
  }
  .canvas {
    position: relative;
    width: 1200px;
    height: 800px;
  }
  .card {
    position: absolute;
    width: 620px;
    height: 354px;
    background: var(--card);
    border-radius: 22px;
    overflow: hidden;
    box-shadow: 0 12px 30px rgba(0,0,0,0.35);
  }
  .card--front { left: 290px; top: 34px; }
  .card--back  { left: 290px; top: 412px; }

  /* front */
  .front__logo-name {
    position: absolute;
    left: 70px;
    top: 44px;
    font-size: 22px;
    font-weight: 400;
    color: var(--ink-blue);
    letter-spacing: 0.5px;
    white-space: nowrap;
  }
  .front__illustration {
    position: absolute;
    left: 40px;
    top: 96px;
    width: 250px;
    height: 210px;
    border-radius: 50% 60% 45% 55%;
    background: linear-gradient(135deg, var(--sky-blue) 0%, var(--deep-blue) 100%);
    opacity: 0.85;
  }
  .front__details {
    position: absolute;
    left: 318px;
    top: 60px;
    width: 285px;
    color: var(--ink-blue);
  }
  .front__name {
    margin: 0;
    font-size: 27px;
    font-weight: 900;
    letter-spacing: 0.5px;
    text-transform: uppercase;
    white-space: nowrap;
  }
  .front__title {
    margin: 2px 0 22px;
    font-size: 18px;
    font-weight: 400;
  }
  .contact-list {
    list-style: none;
    margin: 0;
    padding: 0;
  }
  .contact-list__item {
    display: flex;
    align-items: flex-start;
    gap: 10px;
    margin-bottom: 8px;
    font-size: 15px;
    line-height: 1.3;
    white-space: nowrap;
  }
  .contact-list__item--phone {
    font-size: 20px;
    font-weight: 700;
    align-items: center;
  }
  .contact-list__icon {
    flex: none;
    width: 14px;
    height: 14px;
    margin-top: 2px;
    fill: var(--ink-blue);
  }
  .contact-list__item--phone .contact-list__icon { margin-top: 0; }

  /* back */
  .back__illustration {
    position: absolute;
    left: -40px;
    top: 60px;
    width: 410px;
    height: 270px;
    border-radius: 40% 55% 50% 45%;
    background: linear-gradient(160deg, var(--sky-blue) 0%, var(--deep-blue) 100%);
    opacity: 0.85;
  }
  .back__brand {
    position: absolute;
    left: 405px;
    top: 150px;
    width: 190px;
  }
  .back__brand-mark {
    display: block;
    width: 44px;
    height: 44px;
    margin: 0 0 12px 70px;
    border-radius: 50%;
    background: var(--brand-navy);
  }
  .back__brand-lead {
    display: block;
    font-size: 14px;
    font-weight: 700;
    color: var(--brand-grey);
  }
  .back__brand-name {
    display: block;
    font-size: 38px;
    font-weight: 700;
    line-height: 1.05;
    color: var(--brand-navy);
    text-transform: uppercase;
    letter-spacing: 0.5px;
  }
</style>
</head>
<body>
<main class="canvas">
  <section class="card card--front" aria-label="Card front">
    <div class="front__logo-name">harrowfields.net.au</div>
    <div class="front__illustration" role="img" aria-label="Decorative swirling blue horse head illustration"></div>
    <div class="front__details">
      <h1 class="front__name">Daniel Prescott</h1>
      <p class="front__title">Founder &amp; CEO</p>
      <ul class="contact-list">
        <li class="contact-list__item">
          <svg class="contact-list__icon" viewBox="0 0 24 24" aria-hidden="true"><path d="M12 2a7 7 0 0 0-7 7c0 5 7 13 7 13s7-8 7-13a7 7 0 0 0-7-7zm0 9.5A2.5 2.5 0 1 1 12 6.5a2.5 2.5 0 0 1 0 5z"/></svg>
          <span>27 Lindqvist Rd<br>Marrowbank Q 4587</span>
        </li>
        <li class="contact-list__item contact-list__item--phone">
          <svg class="contact-list__icon" viewBox="0 0 24 24" aria-hidden="true"><path d="M6.6 10.8a15 15 0 0 0 6.6 6.6l2.2-2.2a1 1 0 0 1 1-.25 11.4 11.4 0 0 0 3.6.57 1 1 0 0 1 1 1V20a1 1 0 0 1-1 1A17 17 0 0 1 3 4a1 1 0 0 1 1-1h3.5a1 1 0 0 1 1 1c0 1.250.2 2.45.57 3.57a1 1 0 0 1-.25 1z"/></svg>
          <span>1300 48 62 90</span>
        </li>
        <li class="contact-list__item">
          <svg class="contact-list__icon" viewBox="0 0 24 24" aria-hidden="true"><path d="M2 5h20v14H2zm2 2v.5l8 5 8-5V7z"/></svg>
          <span>office@harrowfields.net.au</span>
        </li>
        <li class="contact-list__item">
          <svg class="contact-list__icon" viewBox="0 0 24 24" aria-hidden="true"><path d="M12 2a10 10 0 1 0 0 20 10 10 0 0 0 0-20zm0 2c1 0 2.3 2 2.8 5H9.2C9.7 6 11 4 12 4zm-7.7 7h3.8a17 17 0 0 0 0 2H4.3a8 8 0 0 1 0-2zm5 0h5.4a15 15 0 0 1 0 2H9.3a15 15 0 0 1 0-2zm6.6 0h3.8a8 8 0 0 1 0 2h-3.8a17 17 0 0 0 0-2zM12 20c-1 0-2.3-2-2.8-5h5.6c-.5 3-1.8 5-2.8 5z"/></svg>
          <span>harrowfields.net.au</span>
        </li>
      </ul>
    </div>
  </section>

  <section class="card card--back" aria-label="Card back">
    <div class="back__illustration" role="img" aria-label="Large decorative swirling blue horse head illustration"></div>
    <div class="back__brand">
      <span class="back__brand-mark" aria-hidden="true"></span>
      <span class="back__brand-lead">Distributers of</span>
      <span class="back__brand-name">trailgem</span>
    </div>
  </section>
</main>
</body>
</html>
```